Tarvel Kite Corporate Site Template/Blog Design

Company Info: Tarvel Kite Robotics is a San Francisco based start-up and spin-off of Halvern Drury University Robotics Institute. Our mission is to transform the consumer experience through personal robotics technology.

Our first public brand, uPickGizmos.example (UPG), used these technologies to develop engaging toy and gaming category innovations that enhance the way children play and interact with new technologies.

This assignment is about the Tarvel Kite Robotic corporate identity and not about UPG

The company is transitioning to include higher end consumer electronics and personal robotics products lines within the next few years, and we would like to establish a more formal corporate identity. Attached please find a user flow of the design needed, as well as our current logo.

High Res .EPS Link below:

https://tkrobotics.filevault.example/shared/static/a730cbe12fd9931e27ab.eps

Design Vision: Tarvel Kite Robotics is in search of a simple, clean and easily updateable corporate website with an integrated blog. The company's current public profile is primarily UPG with an emphasis our children's toy lines Wudle and Clankoras. Although you should be aware of these toy sites, please do not let them influence your design. What we are looking for is more of a blend of scientific and cool.

We would like to see a site template and design that is clean and approachable. It also needs to be able to support a CMS platform as we need the ability to allow our marketing team to update and manage content as well as add additional features such as video and ecommerce in the future as the company grows. These designs should also work well with Facebook and Twitter.

Attached is an image of our corporate card. The current color scheme is very basic but the design should complement them.

The final design and layout should communicate a sleek, innovative and technologically saavy consumer electronics and personal robotics company. Again, we are a consumer oriented organization but the key audiences for this site will be investors, media, retail and biz dev partners, and potential employees

Target Market(s)

Investors, Biz dev and other partners, retail, Media, employees. Consumers secondary

Industry/Entity Type

Electronics

Requirements
Must have
• The site must have all of the tabs that we have identified in the attached user flow.

The design must be able to support a backend content management system. We currently have an upgraded PageRo account, and can provide access if needed but will soon transition to our own site. we are open to your recommendations. Our objective is to be able to easily update the content without relying on a developer.

Font should be sleek. And not bubbly.
Nice to have
• Clean site design. Simple layouts. A blend between scientific and cool. Easy to navigate tabs and sub tabs. forward thinking imagery

Should not have
• Nothing complex on the Homepage- should be very simple. No cartoonish robots, bright colors. Little or no use of humans in stock photos. No competative products or copy. Toys should be under product tabs, and not featured on the homepage as in our initial design efforts we felt that the two were aesthetically polarizing. Just to confirm, the Tarvel Kite Corporate site should serve more as the parent site, and the toy lines should stay under the sub navs on the product page.

```html
<!DOCTYPE html>
<html lang="en">
<head>
<meta charset="utf-8">
<title>Tarvel Kite Robotics</title>
<link href="https://fonts.googleapis.com/css2?family=Source+Sans+3:ital,wght@0,400;0,600;0,700;1,400&display=swap" rel="stylesheet">
<style>
  :root {
    --ink: #2b2724;
    --body: #333333;
    --accent: #2a8fb8;
    --accent-light: #5cc3e6;
    --nav-top: #5cc6e6;
    --nav-bottom: #1b8db6;
    --rule: #d6d6d6;
    --panel-border: #dddddd;
    --badge: #9b2430;
    --page: #ffffff;
  }
  * { margin: 0; padding: 0; box-sizing: border-box; }
  html, body { width: 759px; height: 1200px; overflow: hidden; background: var(--page); }
  body { font-family: "Source Sans 3", Arial, sans-serif; color: var(--body); position: relative; }

  /* header */
  .site-header { position: absolute; left: 0; top: 0; width: 759px; height: 98px;
    background: linear-gradient(#ffffff, #f3f4f5); }
  .utility-links { position: absolute; top: 10px; right: 18px; display: flex; gap: 14px; font-size: 12.5px; color: #333; list-style: none; }
  .utility-links li { display: flex; align-items: center; gap: 5px; }
  .utility-links svg { width: 5px; height: 6px; }
  .brand { position: absolute; left: 22px; top: 38px; color: var(--ink); font-weight: 700; line-height: 1; }
  .brand .brand-main { font-size: 31px; letter-spacing: -0.3px; display: block; }
  .brand .brand-sub { font-size: 15px; font-weight: 400; letter-spacing: 10.4px; display: block; margin-top: 1px; }
  .main-nav { position: absolute; left: 295px; top: 57px; width: 464px; height: 41px; }
  .main-nav svg { position: absolute; inset: 0; }
  .main-nav ul { position: absolute; inset: 0; list-style: none; }
  .main-nav li { position: absolute; top: 13px; transform: translateX(-50%); color: #fff; font-size: 12px; font-weight: 700; white-space: nowrap; }

  /* hero */
  .hero { position: absolute; left: 1px; top: 98px; width: 757px; height: 234px; border: 1px solid var(--panel-border);
    border-radius: 6px; overflow: hidden; background: linear-gradient(90deg, #fafafa, #f1f2f3); }
  .hero-visual { position: absolute; right: 0; top: 0; width: 430px; height: 234px;
    background: linear-gradient(100deg, rgba(241,242,243,0) 0%, #e7eaec 25%, #d9dfe3 60%, #e3e6e8 100%); }
  .hero-title { position: absolute; left: 55px; top: 146px; font-size: 30px; font-weight: 400; color: var(--accent-light); line-height: 1; }
  .hero-subtitle { position: absolute; left: 56px; top: 181px; font-size: 28px; font-weight: 400; color: var(--ink); line-height: 1; }
  .hero-text { position: absolute; left: 60px; top: 220px; font-size: 12px; line-height: 19.5px; color: #222; }

  /* headings and copy */
  .section-title { position: absolute; display: flex; align-items: center; gap: 8px; color: var(--accent);
    font-size: 15px; font-weight: 400; text-transform: uppercase; white-space: nowrap; }
  .section-title svg { width: 5px; height: 6px; }
  .copy { position: absolute; font-size: 10px; line-height: 15.5px; color: var(--body); text-align: justify; hyphens: auto; -webkit-hyphens: auto; }
  .copy p + p { margin-top: 15.5px; }
  .more-info { position: absolute; font-size: 10px; font-style: italic; color: var(--accent); text-decoration: underline; }
  .article-title { position: absolute; font-size: 17px; font-weight: 700; color: var(--ink); }
  .divider { position: absolute; height: 0; border-top: 1px dashed var(--rule); }

  .tech-visual { position: absolute; left: 460px; top: 576px; width: 250px; height: 109px; border: 3px solid #e4e4e4;
    background: linear-gradient(#eef4fb, #6aa8e6 60%, #1f6fd0); }
  .news-date { font-weight: 700; color: var(--ink); }

  /* footer */
  .footer-links { position: absolute; list-style: none; font-size: 9.5px; color: var(--accent); text-transform: uppercase; line-height: 23.2px; }
  .footer-brand { position: absolute; left: 456px; top: 1016px; color: #555; font-weight: 700; line-height: 1; }
  .footer-brand .brand-main { font-size: 25px; letter-spacing: -0.3px; display: block; }
  .footer-brand .brand-sub { font-size: 12px; font-weight: 400; letter-spacing: 8px; display: block; margin-top: 1px; }
  .footer-contact { position: absolute; left: 456px; top: 1063px; font-size: 8.5px; color: #222; line-height: 15.8px; }
  .footer-contact .phone-main { font-size: 9.5px; }
  .copyright { position: absolute; left: 456px; top: 1114px; font-size: 8px; color: #222; }
  .partner-badge { position: absolute; left: 666px; top: 1024px; width: 66px; height: 66px; background: #e4e4e4; }
  .social { position: absolute; top: 1153px; left: 454px; display: flex; gap: 14px; list-style: none; }
  .social li { width: 25px; height: 25px; border-radius: 50%; background: radial-gradient(circle at 40% 35%, #d0d0d0, #7b7b7b); }
</style>
</head>
<body>

<header class="site-header">
  <ul class="utility-links">
    <li><svg viewBox="0 0 6 7"><path d="M0 0 L6 3.5 L0 7Z" fill="#2a8fb8"/></svg>Sales</li>
    <li><svg viewBox="0 0 6 7"><path d="M0 0 L6 3.5 L0 7Z" fill="#2a8fb8"/></svg>Press</li>
    <li><svg viewBox="0 0 6 7"><path d="M0 0 L6 3.5 L0 7Z" fill="#2a8fb8"/></svg>Jobs</li>
    <li><svg viewBox="0 0 6 7"><path d="M0 0 L6 3.5 L0 7Z" fill="#2a8fb8"/></svg>Support</li>
  </ul>
  <div class="brand"><span class="brand-main">TARVEL KITE</span><span class="brand-sub">ROBOTICS</span></div>
  <nav class="main-nav">
    <svg viewBox="0 0 464 41" preserveAspectRatio="none">
      <defs>
        <linearGradient id="navFill" x1="0" y1="0" x2="0" y2="1">
          <stop offset="0" stop-color="#5cc6e6"/>
          <stop offset="1" stop-color="#1b8db6"/>
        </linearGradient>
      </defs>
      <path d="M14 0 H464 V41 H0 Z" fill="url(#navFill)"/>
      <g stroke="#8fd8f0" stroke-width="1" opacity=".7">
        <line x1="106" y1="0" x2="92" y2="41"/>
        <line x1="200" y1="0" x2="186" y2="41"/>
        <line x1="296" y1="0" x2="282" y2="41"/>
        <line x1="370" y1="0" x2="356" y2="41"/>
      </g>
    </svg>
    <ul>
      <li style="left:57px">HOME</li>
      <li style="left:148px">ABOUT US</li>
      <li style="left:246px">PRODUCTS</li>
      <li style="left:329px">NEWS</li>
      <li style="left:411px">CONTACT</li>
    </ul>
  </nav>
</header>

<section class="hero">
  <div class="hero-visual" role="img" aria-label="Photograph of a colourful ball-and-stick molecule model"></div>
</section>
<h1 class="hero-title">Building Robots</h1>
<p class="hero-subtitle">facinating about science</p>
<p class="hero-text">Equipped with his five senses, man explores<br>the universe around him and calls<br>the adventure science</p>

<h2 class="section-title" style="left:18px;top:356px"><svg viewBox="0 0 6 7"><path d="M0 0 L6 3.5 L0 7Z" fill="#333"/></svg>Our Researches</h2>
<div class="copy" style="left:15px;top:387px;width:148px">Lorem ipsum dolor sit amet, consectetur adipisicing elit, sed do eiusmod tempor incididunt ut labore et dolore magna aliqua. Ut enim ad minim veniam, quis nostrud exercitation ullamco laboris.</div>
<a class="more-info" style="left:15px;top:494px">more info</a>

<h2 class="section-title" style="left:198px;top:356px"><svg viewBox="0 0 6 7"><path d="M0 0 L6 3.5 L0 7Z" fill="#333"/></svg>Recent Experiments</h2>
<div class="copy" style="left:198px;top:387px;width:148px">Lorem ipsum dolor sit amet, consectetur adipisicing elit, sed do eiusmod tempor incididunt ut labore et dolore magna aliqua. Ut enim ad minim veniam, quis nostrud exercitation ullamco laboris.</div>
<a class="more-info" style="left:198px;top:494px">more info</a>

<h2 class="section-title" style="left:388px;top:356px"><svg viewBox="0 0 6 7"><path d="M0 0 L6 3.5 L0 7Z" fill="#333"/></svg>Research Center</h2>
<div class="copy" style="left:386px;top:387px;width:148px">Lorem ipsum dolor sit amet, consectetur adipisicing elit, sed do eiusmod tempor incididunt ut labore et dolore magna aliqua. Ut enim ad minim veniam, quis nostrud exercitation ullamco laboris.</div>
<a class="more-info" style="left:384px;top:494px">more info</a>

<h2 class="section-title" style="left:584px;top:356px"><svg viewBox="0 0 6 7"><path d="M0 0 L6 3.5 L0 7Z" fill="#333"/></svg>Robotics Enquiries</h2>
<div class="copy" style="left:585px;top:387px;width:148px">Lorem ipsum dolor sit amet, consectetur adipisicing elit, sed do eiusmod tempor incididunt ut labore et dolore magna aliqua. Ut enim ad minim veniam, quis nostrud exercitation ullamco laboris.</div>
<a class="more-info" style="left:584px;top:494px">more info</a>

<h2 class="article-title" style="left:13px;top:543px">Welcome to Tarvel Kite Robotics Institute</h2>
<div class="copy" style="left:14px;top:570px;width:408px">
  <p>Velit at et ac nascetur faucibus nec dictumst fringilla lacus nonummy. Primis luctus adipiscing risus, nonummy. Ut viverra vestibulum. Vitae sit rhoncus maecenas, praesent quisque ullamcorper lobortis. Condimentum luctus dignissim scelerisque.</p>
  <p>Consequat pede. Urna placerat nascetur sem. Commodo malesuada egestas est ad. Mus magna. Elit pede, primis hymenaeos blandit luctus justo platea magnis. Malesuada.</p>
  <p>Risus platea habitant habitasse ornare. Nostra bibendum montes leo elit nisi mollis curabitur tellus dictumst pulvinar neque Ridiculus, suspendisse placerat suspendisse. Purus fames vestibulum cursus donec euismod dignissim facilisis. Etiam platea adipiscing posuere rutrum adipiscing erat leo. Etiam risus tincidunt tortor gravida duis tristique per senectus.</p>
</div>
<a class="more-info" style="left:14px;top:754px">more info</a>
<div class="divider" style="left:13px;top:786px;width:412px"></div>

<h2 class="article-title" style="left:12px;top:806px">Building Robots, facinating about Science</h2>
<div class="copy" style="left:13px;top:839px;width:408px">
  <p>Velit at et ac nascetur faucibus nec dictumst fringilla lacus nonummy. Primis luctus adipiscing risus, nonummy. Ut viverra vestibulum. Vitae sit rhoncus maecenas, praesent quisque ullamcorper lobortis. Condimentum luctus dignissim scelerisque.</p>
  <p>Consequat pede. Urna placerat nascetur sem. Commodo malesuada egestas est ad. Mus magna. Elit pede, primis hymenaeos blandit luctus justo platea magnis. Malesuada.</p>
</div>
<a class="more-info" style="left:12px;top:944px">more info</a>

<h2 class="section-title" style="left:460px;top:543px"><svg viewBox="0 0 6 7"><path d="M0 0 L6 3.5 L0 7Z" fill="#333"/></svg>Advanced Technologies</h2>
<div class="tech-visual" role="img" aria-label="Illustration of a blue network globe made of linked nodes"></div>
<div class="copy" style="left:460px;top:699px;width:281px">Lorem ipsum dolor sit amet, consectetur adipisicing elit, sed do eiusmod tempor incididunt ut labore et dolore magna aliqua. Ut enim ad minim veniam, quis nostrud exercitation ullamco laboris.</div>
<a class="more-info" style="left:459px;top:755px">more info</a>
<div class="divider" style="left:460px;top:786px;width:280px"></div>

<h2 class="section-title" style="left:460px;top:805px"><svg viewBox="0 0 6 7"><path d="M0 0 L6 3.5 L0 7Z" fill="#333"/></svg>Latest News</h2>
<div class="copy" style="left:460px;top:836px;width:281px">
  <div class="news-date">April 25, 2012</div>
  Lorem ipsum dolor sit amet, consectetur adipisicing elit, sed do eiusmod tempor incididunt ut labore et dolore magna aliqua.
</div>
<div class="copy" style="left:460px;top:895px;width:281px">
  <div class="news-date">April 25, 2012</div>
  Lorem ipsum dolor sit amet, consectetur adipisicing elit, sed do eiusmod tempor incididunt ut labore et dolore magna aliqua.
</div>
<a class="more-info" style="left:461px;top:953px">more info</a>

<footer>
  <div class="divider" style="left:13px;top:989px;width:735px"></div>
  <ul class="footer-links" style="left:33px;top:1015px">
    <li>Retailer Listing</li><li>Direct From Us</li><li>Robot Cloud Services</li><li>News</li><li>Robot Blog</li><li>Press Releases</li>
  </ul>
  <ul class="footer-links" style="left:194px;top:1015px">
    <li>History</li><li>Vision</li><li>Executive Team</li><li>Partners</li><li>Personal Robotics</li><li>Toys &amp; Games</li>
  </ul>
  <div class="footer-brand"><span class="brand-main">TARVEL KITE</span><span class="brand-sub">ROBOTICS</span></div>
  <div class="footer-contact">
    <div class="phone-main">xxxxx-xxxxx-xxxxx-xxxxx</div>
    <div>xxxxx-xxxxx-xxxxx</div>
    <div>xxxxx-xxxxx-xxxxx-xxxxx</div>
  </div>
  <p class="copyright">Copyrights Reserved 2012 @ Tarvel Kite Robotics</p>
  <div class="partner-badge" role="img" aria-label="Partner institute badge"></div>
  <ul class="social" aria-label="Social links">
    <li></li><li></li><li></li><li></li>
  </ul>
</footer>

</body>
</html>
```